Black Matte card with samurai logo which I would like it to be textured and company name on one side and on the other side I would like the company information with the reno (Face logo) Sushi logo. Double Sided card.

majority customers are University students, University sororities and fraternities.

It Company

Reno Sushi
317 W. Harlow Ave
Tucson, AZ 85042
Phone (520)413-6271
Fax (520)357-1846
E-mail: Renosushidesert@mailbox-example.com
FB: Renosushidesert
Twitter: Renosushidesert

• Present Normal

```html
<!DOCTYPE html>
<html lang="en">
<head>
<meta charset="utf-8">
<title>Reno Sushi – Business Card</title>
<link rel="stylesheet" href="https://fonts.googleapis.com/css2?family=Open+Sans:wght@400;600&display=swap">
<style>
  :root {
    --stage: #e8e5e1;
    --card-black: #141414;
    --card-charcoal: #2c2c2c;
    --card-white: #ffffff;
    --brand-red: #b5232b;
    --deep-red: #7d1419;
    --ink: #4a4a4a;
    --rule: #cfcfcf;
    --wave-black: #1d1d1d;
  }
  * { box-sizing: border-box; margin: 0; padding: 0; }
  html, body {
    width: 1176px;
    height: 1200px;
    overflow: hidden;
    background: var(--stage);
    font-family: "Open Sans", Arial, sans-serif;
  }
  .card {
    position: absolute;
    border-radius: 30px;
    overflow: hidden;
  }

  /* Front side */
  .card--front {
    left: 22px; top: 42px;
    width: 953px; height: 541px;
    background: linear-gradient(180deg, var(--card-charcoal) 0%, var(--card-black) 55%, var(--card-charcoal) 100%);
  }
  .front__emblem {
    position: absolute;
    left: 304px; top: 87px;
    width: 340px; height: 335px;
    background: radial-gradient(circle at 50% 45%, #e9e9e9 0%, #8d8d8d 55%, rgba(181,35,43,0.55) 100%);
    border-radius: 18px;
  }
  .front__name {
    position: absolute;
    left: 0; right: 0; top: 428px;
    text-align: center;
    font-size: 66px;
    font-weight: 400;
    color: var(--brand-red);
    letter-spacing: 1px;
  }

  /* Back side */
  .card--back {
    left: 209px; top: 628px;
    width: 950px; height: 542px;
    background: var(--card-white);
  }
  .back__emblem {
    position: absolute;
    left: 128px; top: 52px;
    width: 240px; height: 205px;
    background: radial-gradient(circle at 50% 45%, #6a6a6a 0%, #2a2a2a 60%, rgba(181,35,43,0.7) 100%);
    border-radius: 14px;
  }
  .back__name {
    position: absolute;
    left: 88px; width: 320px; top: 272px;
    text-align: center;
    font-size: 48px;
    font-weight: 400;
    color: var(--brand-red);
    line-height: 1.1;
  }
  .back__divider {
    position: absolute;
    left: 416px; top: 130px;
    width: 1px; height: 208px;
    background: var(--rule);
  }
  .contact {
    position: absolute;
    left: 447px; top: 130px;
    list-style: none;
  }
  .contact__item {
    display: flex;
    align-items: center;
    height: 38px;
    font-size: 22px;
    color: var(--ink);
  }
  .contact__item--email { font-size: 20px; }
  .contact__icon {
    width: 26px; height: 26px;
    margin-right: 12px;
    flex: none;
  }
  .address {
    position: absolute;
    left: 447px; top: 272px;
    font-size: 22px;
    line-height: 34px;
    color: var(--ink);
    font-style: normal;
  }
  .back__waves {
    position: absolute;
    left: 0; top: 0;
    width: 950px; height: 542px;
  }
  .social {
    position: absolute;
    left: 652px; top: 452px;
    list-style: none;
  }
  .social__item {
    display: flex;
    align-items: center;
    height: 34px;
    font-size: 21px;
    color: var(--card-white);
  }
  .social__mark {
    width: 22px; height: 22px;
    margin-right: 10px;
    background: #5b6f9e;
    border-radius: 3px;
  }
  .social__mark--alt { background: #4aa6d8; }
</style>
</head>
<body>

<section class="card card--front" aria-label="Card front">
  <div class="front__emblem" role="img" aria-label="Samurai mascot emblem holding a sword and a red fish"></div>
  <p class="front__name">Reno Sushi</p>
</section>

<section class="card card--back" aria-label="Card back">
  <svg class="back__waves" viewBox="0 0 950 542" aria-hidden="true">
    <defs>
      <linearGradient id="redBand" x1="0" y1="0" x2="1" y2="0">
        <stop offset="0" stop-color="#b5232b"/>
        <stop offset="1" stop-color="#7d1419"/>
      </linearGradient>
    </defs>
    <path d="M0,452 C260,392 520,398 950,318" fill="none" stroke="#7d1419" stroke-width="4"/>
    <path d="M0,472 C260,412 520,418 950,340 L950,542 L0,542 Z" fill="url(#redBand)"/>
    <path d="M0,508 C300,458 540,430 950,372 L950,542 L0,542 Z" fill="#ffffff"/>
    <path d="M0,522 C300,474 540,446 950,386 L950,542 L0,542 Z" fill="#1d1d1d"/>
  </svg>

  <div class="back__emblem" role="img" aria-label="Samurai mascot emblem holding a sword and a red fish"></div>
  <p class="back__name">Reno Sushi</p>
  <div class="back__divider"></div>

  <ul class="contact">
    <li class="contact__item">
      <svg class="contact__icon" viewBox="0 0 26 26" aria-hidden="true">
        <circle cx="13" cy="13" r="11" fill="none" stroke="#b5232b" stroke-width="2"/>
        <path d="M9,7 L12,10 L10.5,12 C11.5,14 12.5,15 14,15.5 L16,14 L19,17 L17,19 C12,19 7,14 7,9 Z" fill="#b5232b"/>
      </svg>
      (520)413-6271
    </li>
    <li class="contact__item">
      <svg class="contact__icon" viewBox="0 0 26 26" aria-hidden="true">
        <rect x="7" y="3" width="12" height="8" fill="none" stroke="#b5232b" stroke-width="2"/>
        <rect x="3" y="10" width="20" height="10" rx="2" fill="#b5232b"/>
        <rect x="8" y="16" width="10" height="7" fill="#fff" stroke="#b5232b" stroke-width="1.5"/>
      </svg>
      (520)357-1846
    </li>
    <li class="contact__item contact__item--email">
      <svg class="contact__icon" viewBox="0 0 26 26" aria-hidden="true">
        <rect x="2" y="6" width="22" height="15" rx="2" fill="#b5232b"/>
        <path d="M3,7 L13,15 L23,7" fill="none" stroke="#fff" stroke-width="1.8"/>
      </svg>
      Renosushidesert@mailbox-example.com
    </li>
  </ul>

  <address class="address">
    Reno Sushi 317 W. Harlow Ave<br>
    Tucson, AZ 85042
  </address>

  <ul class="social">
    <li class="social__item"><span class="social__mark"></span>Renosushidesert</li>
    <li class="social__item"><span class="social__mark social__mark--alt"></span>Renosushidesert</li>
  </ul>
</section>

</body>
</html>
```